Business Card Design

We are a company that provides stump grinding services for residential and commercial clients. Looking for a simple business card design that may have some type of graphic on the card that will tie in with the Tamsen name(Grizzly Bear, Paw Print, etc) . Possibly some foliage wrapping around part of the card? Would like to have a simple design that stands out because it is unique. We are working on getting the website set up and there is a simple graphic on the top of the page that came to mind when I mentioned the leaves.

Industry/Entity Type

Business

Contact Information for Business Card

Tamsen Stump Grinding 303-257-4788KodiakStumps.Com

Font styles to use
Serif

Requirements
Must have
• Business name
• Website Address
• Phone Number
Nice to have
• Graphics that would be associated with a Tamsen bear.
Should not have
• Nothing frilly

```html
<!DOCTYPE html>
<html lang="en">
<head>
<meta charset="utf-8">
<title>Tamsen Stump Grinding – Business Card</title>
<link rel="stylesheet" href="https://fonts.googleapis.com/css2?family=Josefin+Sans:wght@400&family=Open+Sans:wght@400&display=swap">
<style>
  :root {
    --stage: #1c1c1c;
    --card-blue: #4f8bcb;
    --card-blue-light: #6ba5d9;
    --card-blue-deep: #3f73ba;
    --ink-white: #ffffff;
  }
  * { margin: 0; padding: 0; box-sizing: border-box; }
  html, body { width: 1200px; height: 900px; overflow: hidden; }
  body { background: var(--stage); position: relative; }

  .card {
    position: absolute;
    top: 170px;
    width: 346px;
    height: 560px;
    color: var(--ink-white);
    text-align: center;
  }

  /* Front */
  .card--front { left: 259px; background: var(--card-blue); }
  .front-band {
    position: absolute; left: 0; width: 100%;
    background: linear-gradient(90deg, var(--card-blue-deep), var(--card-blue-light));
  }
  .front-band--top { top: 0; height: 30px; }
  .front-band--bottom { bottom: 0; height: 27px; }

  .brand-ring {
    position: absolute; left: 93px; top: 104px;
    width: 160px; height: 160px;
    border: 10px solid var(--ink-white);
    border-radius: 50%;
  }
  .brand-name {
    position: absolute; left: 0; width: 100%;
    font-family: "Josefin Sans", sans-serif;
    font-weight: 400;
    color: var(--ink-white);
  }
  .brand-name--main { top: 276px; font-size: 33px; letter-spacing: 0.5px; }
  .brand-name--sub { top: 318px; font-size: 18px; letter-spacing: 17px; padding-left: 17px; }

  .contact {
    position: absolute; left: 0; top: 386px; width: 100%;
    font-family: "Open Sans", sans-serif;
    font-size: 18px; line-height: 26px;
  }
  .contact-line { display: flex; justify-content: center; align-items: center; gap: 8px; }
  .contact-line svg { width: 16px; height: 16px; fill: none; stroke: var(--ink-white); stroke-width: 2; }
  .contact-line .icon-phone { fill: var(--ink-white); stroke: none; }

  /* Back */
  .card--back {
    left: 631px;
    background: linear-gradient(90deg, var(--card-blue-light) 0%, var(--card-blue) 50%, var(--card-blue-deep) 100%);
  }
  .back-ring {
    position: absolute; left: 45px; top: 152px;
    width: 258px; height: 258px;
    border: 12px solid var(--ink-white);
    border-radius: 50%;
    display: flex; align-items: center; justify-content: center;
  }
  .back-ring .brand-name { position: static; font-size: 40px; }
  .back-url {
    position: absolute; left: 0; top: 476px; width: 100%;
    font-family: "Open Sans", sans-serif; font-size: 17px;
  }
</style>
</head>
<body>
  <section class="card card--front">
    <div class="front-band front-band--top"></div>
    <div class="brand-ring"></div>
    <div class="brand-name brand-name--main">TAMSEN STUMP</div>
    <div class="brand-name brand-name--sub">GRINDING</div>
    <div class="contact">
      <div class="contact-line">
        <svg class="icon-phone" viewBox="0 0 24 24" aria-hidden="true"><path d="M2 8c0-3 5-5 10-5s10 2 10 5v2h-5V7.5c-3-1-7-1-10 0V10H2zM6 11h12l3 9H3z"/></svg>
        <span>303-555-0146</span>
      </div>
      <div class="contact-line">
        <svg viewBox="0 0 24 24" aria-hidden="true"><path d="M10 14a4 4 0 0 0 6 0l4-4a4 4 0 0 0-6-6l-1 1M14 10a4 4 0 0 0-6 0l-4 4a4 4 0 0 0 6 6l1-1"/></svg>
        <span>TamsenStumps.Com</span>
      </div>
    </div>
    <div class="front-band front-band--bottom"></div>
  </section>

  <section class="card card--back">
    <div class="back-ring"><span class="brand-name">TAMSEN</span></div>
    <div class="back-url">TamsenStumps.Com</div>
  </section>
</body>
</html>
```